New Business Card Design for Manufacturing

We are an engineering/manufacturing company that offers Advanced machining/assembly/engineering services, as well as innovative products for the heavy duty engine cooling markets.

We are looking to get a new business card designed that is clean and modern looking, but still fits the wide range of technical/skilled work we do.

- We hope to use this design as the base for other design work in new Presentations, web, and print work.

Industry/Entity Type

Engineering

Contact Information for Business Card

Our preferred color of blue is (RGB) 22/71/159 but can vary slightly from that color. Our content will be our Logo and full company name (Vantrell Forge Works, Inc.), company address, name, job title, phone number with extension, cell number, fax number, website, and email address on the cards.
We'd like the full company name next to the logo, but we are open to other interpretations of that layout.
Preferably, we would like the back side to be clean with just our logo, and the front to contain all of the contact information.

Colors
2f74b4
0355a3
85abd2

Requirements
Must have
• - Logo, company name, needed content - We are open to interpretation beyond that.
• - Standard size business card.
• - Horizontal orientation.
• - Enough space for lengthy names / job titles (for example, a job title could read "Directory of Human Resources" or "V.P. of Governmental Affairs"). We need this to look clean, whether the title be short (CEO) or long (as described above).

```html
<!DOCTYPE html>
<html lang="en">
<head>
<meta charset="utf-8">
<title>Vantrell Forge Works – Business Card</title>
<link href="https://fonts.googleapis.com/css2?family=Lato:wght@400;700;900&display=swap" rel="stylesheet">
<style>
  :root {
    --brand-blue: #16479f;
    --brand-blue-mid: #0355a3;
    --brand-blue-soft: #85abd2;
    --ink-grey: #3a3a3a;
    --card-white: #ffffff;
    --stage: #1e1e20;
  }
  * { box-sizing: border-box; margin: 0; padding: 0; }
  html, body {
    width: 1200px; height: 738px; overflow: hidden;
    background: var(--stage);
    font-family: "Lato", sans-serif;
  }
  .stage {
    width: 1200px; height: 738px;
    display: flex; align-items: center; justify-content: center; gap: 40px;
  }
  .card {
    width: 520px; height: 297px; position: relative; overflow: hidden;
    border-radius: 3px;
  }
  /* Back side */
  .card--back {
    background: var(--brand-blue);
    display: flex; align-items: center; justify-content: center;
  }
  .brand {
    display: flex; align-items: center; gap: 12px;
    font-weight: 900; letter-spacing: 0.04em; text-transform: uppercase;
  }
  .brand__mark { width: 22px; height: 22px; flex: none; }
  .card--back .brand { color: var(--card-white); font-size: 22px; }
  .card--back .brand__mark { background: var(--card-white); width: 26px; height: 26px; }

  /* Front side */
  .card--front { background: var(--card-white); }
  .card--front .brand {
    position: absolute; left: 34px; top: 34px;
    color: var(--brand-blue); font-size: 16px;
  }
  .card--front .brand__mark { background: var(--brand-blue); }
  .person { position: absolute; left: 34px; top: 128px; }
  .person__name {
    color: var(--brand-blue); font-size: 21px; font-weight: 700; letter-spacing: 0.06em;
    text-transform: uppercase;
  }
  .person__title { color: var(--ink-grey); font-size: 13px; margin-top: 2px; }

  .contact {
    position: absolute; left: 34px; right: 30px; top: 196px;
    display: flex; justify-content: space-between; align-items: flex-end;
    font-size: 12.5px; color: var(--ink-grey); line-height: 1.35;
  }
  .contact__label { color: var(--brand-blue); }
  .contact__address { text-align: left; }

  .rule {
    position: absolute; left: 0; right: 0; top: 246px; height: 2px;
    background: var(--brand-blue);
  }
  .band {
    position: absolute; left: 0; right: 0; bottom: 0; height: 44px;
    background: var(--brand-blue);
    display: flex; align-items: center; justify-content: center;
    color: var(--card-white); font-size: 13px; letter-spacing: 0.22em;
  }
</style>
</head>
<body>
<main class="stage">
  <section class="card card--back" aria-label="Card back">
    <div class="brand"><span class="brand__mark"></span><span>Vantrell Forge Works, Inc.</span></div>
  </section>

  <section class="card card--front" aria-label="Card front">
    <div class="brand"><span class="brand__mark"></span><span>Vantrell Forge Works, Inc.</span></div>

    <div class="person">
      <h1 class="person__name">Darren Holcomb</h1>
      <p class="person__title">Directory of Human Resources</p>
    </div>

    <div class="contact">
      <div class="contact__phones">
        <div><span class="contact__label">Phone:</span> 1234- ext</div>
        <div><span class="contact__label">Cell:</span> 555-318-4406</div>
      </div>
      <div class="contact__mail">
        <div><span class="contact__label">fax:</span> (555)318-4406</div>
        <div>dholcomb@vantrellforge.com</div>
      </div>
      <div class="contact__address">
        <div>480 Kessler Park Rd.</div>
        <div>Lakemont, FL 33512</div>
      </div>
    </div>

    <div class="rule"></div>
    <footer class="band">www.vantrellforge.com</footer>
  </section>
</main>
</body>
</html>
```